Business card design for Virtual Assistance company

I need a business card designed for my virtual assistance company. We are a small company who services primarily C-level executive clients. The card needs to be double sided with the following contact information on the back:
Melissa Thornbury
Owner/CEO
info@rkpadvisory.net
www.rkpadvisory.net
555.302.9817

The front side should just have the company name incorporated: "RKP Advisory" and "virtual assistance"

The card should be simplistic, but eye catching and should speak to high level executives. Our primary focus areas consist of executive assistance and government contracting.

Target Market(s)

CEOs and executives

Contact Information for Business Card

see project description. phone, email, website.

Colors

Designer to choose only greyscale colors for use in the design.

```html
<!DOCTYPE html>
<html lang="en">
<head>
<meta charset="utf-8">
<title>RKP Advisory – Business Card</title>
<link rel="stylesheet" href="https://fonts.googleapis.com/css2?family=Lora:wght@400;700&family=Montserrat:wght@300;400&display=swap">
<style>
  :root {
    --backdrop: #d6d6d6;
    --card: #1b1b1b;
    --ink: #ffffff;
    --ink-soft: #d8d8d8;
    --rule: #bdbdbd;
  }
  * { margin: 0; padding: 0; box-sizing: border-box; }
  html, body { width: 1200px; height: 786px; overflow: hidden; }
  body {
    background: var(--backdrop);
    display: flex;
    align-items: center;
    justify-content: center;
    gap: 48px;
  }
  .card {
    width: 540px;
    height: 309px;
    background: var(--card);
    color: var(--ink);
    position: relative;
    box-shadow: 0 10px 24px rgba(0,0,0,0.25);
  }

  /* Contact side */
  .card--contact {
    display: flex;
    align-items: center;
    padding: 0 0 0 44px;
  }
  .brand {
    width: 200px;
    text-align: center;
    margin-top: 40px;
  }
  .brand__name {
    font-family: "Lora", serif;
    font-weight: 400;
    font-size: 29px;
    letter-spacing: 0.2px;
    line-height: 1;
  }
  .brand__tagline {
    font-family: "Lora", serif;
    font-size: 11.5px;
    letter-spacing: 0.6px;
    color: var(--ink-soft);
    margin-top: 5px;
  }
  .divider {
    width: 1px;
    height: 112px;
    background: var(--rule);
    margin: 0 14px 0 20px;
  }
  .contact__name {
    font-family: "Lora", serif;
    font-weight: 700;
    font-size: 18px;
    line-height: 1.1;
  }
  .contact__title {
    font-family: "Montserrat", sans-serif;
    font-weight: 300;
    font-size: 11.5px;
    color: var(--ink-soft);
    margin: 3px 0 9px;
  }
  .contact__list { list-style: none; }
  .contact__item {
    display: flex;
    align-items: center;
    gap: 8px;
    font-family: "Montserrat", sans-serif;
    font-weight: 300;
    font-size: 11.5px;
    color: var(--ink-soft);
    margin-bottom: 7px;
  }
  .contact__icon { width: 10px; height: 10px; fill: var(--ink); flex: none; }

  /* Name side */
  .card--name {
    display: flex;
    align-items: center;
    justify-content: center;
  }
  .card--name .wordmark {
    font-family: "Lora", serif;
    font-weight: 400;
    font-size: 50px;
    color: var(--ink);
  }
</style>
</head>
<body>
  <section class="card card--contact">
    <div class="brand">
      <div class="brand__name">RKP Advisory</div>
      <div class="brand__tagline">VIRTUAL ASSISTANCE</div>
    </div>
    <div class="divider"></div>
    <div class="contact">
      <div class="contact__name">Melissa Thornbury</div>
      <div class="contact__title">Owner/CEO</div>
      <ul class="contact__list">
        <li class="contact__item">
          <svg class="contact__icon" viewBox="0 0 10 10"><path d="M2 0.5 L3.6 2.6 L2.8 3.6 Q3.8 5.8 6.2 7 L7.3 6.2 L9.5 7.8 L8.5 9.5 Q3.5 9 0.5 2 Z"/></svg>
          <span>555.302.9817</span>
        </li>
        <li class="contact__item">
          <svg class="contact__icon" viewBox="0 0 10 10"><path d="M0 2 H10 V8.5 H0 Z M0.5 2.4 L5 5.6 L9.5 2.4" stroke="#1b1b1b" stroke-width="0.8"/></svg>
          <span>info@rkpadvisory.net</span>
        </li>
        <li class="contact__item">
          <svg class="contact__icon" viewBox="0 0 10 10"><circle cx="5" cy="5" r="4.6"/><path d="M0.5 5 H9.5 M5 0.4 Q2.5 5 5 9.6 M5 0.4 Q7.5 5 5 9.6" stroke="#1b1b1b" stroke-width="0.7" fill="none"/></svg>
          <span>www.rkpadvisory.net</span>
        </li>
      </ul>
    </div>
  </section>

  <section class="card card--name">
    <div class="wordmark">RKP Advisory</div>
  </section>
</body>
</html>
```